Business Card Design

Hi I need a business card designed, we already have the business name logo artwork and would like some concept ideas for the Bus Card layout.
On the back of the card i want to include the products and services that we offer.
We are a Plastics Sheeting manufacture based in Perth Australia.

                                       

We need a BC design for a company called Tarvo Plastics based in Perth Australia.

We supply from DIY to Trade & Industrial  Engineering Markets.

We specialise in:

·         Cut to size panels  (all shapes and sizes)

·         Plastics fabrication & Welding

·         Custom Designs

·         Plastic Repairs

·         PVC Pipe Slotting & PVC Pipe Threading

·         Supplier of all types of engineering plastics and profiles.

Including:           Acrylic / Clarvene

                               Polycarbonate / Dorvil

                               Prismatic Light Diffuser

                               Vantrib

                               HDPE / UHMWPE

                               PVC / PVC Foam

                               Nylon

                               HIPS

```html
<!DOCTYPE html>
<html lang="en">
<head>
<meta charset="utf-8">
<title>Tarvo Plastics – Business Card</title>
<link href="https://fonts.googleapis.com/css2?family=Open+Sans:ital,wght@0,400;0,600;0,700;1,700&display=swap" rel="stylesheet">
<style>
  :root {
    --navy: #1b2a5c;
    --sky: #4aa3d8;
    --dot: #2a8fd0;
    --ink: #4a4a4a;
    --orange: #f08a1c;
    --paper: #ffffff;
    --bg: #e9e9ee;
  }
  * { box-sizing: border-box; margin: 0; padding: 0; }
  html, body { width: 1200px; height: 987px; overflow: hidden; }
  body {
    background: var(--bg);
    font-family: "Open Sans", Arial, sans-serif;
    color: var(--ink);
    position: relative;
  }
  .card {
    position: absolute;
    left: 240px;
    width: 720px;
    height: 440px;
    background: var(--paper);
    border-radius: 26px;
    overflow: hidden;
    box-shadow: 0 6px 18px rgba(0,0,0,0.12);
  }
  .card--front { top: 36px; }
  .card--back { top: 511px; }

  /* Front */
  .brand {
    position: absolute;
    left: 150px; top: 38px;
    display: flex; align-items: center; gap: 16px;
    font-size: 64px; font-weight: 700; color: var(--navy);
    letter-spacing: -1px;
  }
  .brand__square { width: 26px; height: 26px; background: var(--navy); }
  .address {
    position: absolute; left: 48px; top: 150px;
    font-size: 19px; line-height: 28px;
  }
  .contacts {
    position: absolute; left: 48px; top: 216px;
    font-size: 19px; line-height: 30px;
  }
  .contacts li { list-style: none; display: flex; align-items: center; gap: 8px; }
  .contacts .fax { margin-left: 22px; display: inline-flex; align-items: center; gap: 8px; }
  .icon { width: 16px; height: 16px; flex: none; }
  .nameband {
    position: absolute; left: 0; right: 0; top: 318px; height: 52px;
    background: var(--navy);
    border-top: 3px solid var(--paper);
    outline: 2px solid var(--sky);
    outline-offset: 0;
    color: #fff; font-size: 25px; font-weight: 600;
    padding: 6px 48px;
  }
  .nameband .title { font-size: 17px; font-weight: 400; }
  .rule-top, .rule-bottom {
    position: absolute; left: 0; right: 0; height: 2px; background: var(--sky);
  }
  .rule-top { top: 310px; }
  .rule-bottom { top: 376px; }
  .legal {
    position: absolute; left: 48px; top: 392px;
    font-size: 16px;
  }

  /* Back */
  .offer {
    position: absolute; inset: 26px 30px;
    text-align: center;
    color: var(--ink);
  }
  .offer__lead {
    color: var(--navy); font-weight: 700; font-style: italic;
    font-size: 21px; line-height: 27px;
  }
  .offer__heading {
    color: var(--navy); font-weight: 700;
    font-size: 25px; margin: 12px 0 4px;
  }
  .offer__list { font-size: 18px; line-height: 26px; }
  .offer__list li { list-style: none; }
  .offer__list span::before {
    content: "•"; color: var(--dot); margin: 0 4px 0 12px;
  }
  .offer__list span:first-child::before { margin-left: 0; }
</style>
</head>
<body>

<section class="card card--front" aria-label="Business card front">
  <div class="brand"><span class="brand__square"></span>Tarvo Plastics</div>

  <div class="address">
    <p>Unit 4/18 Harrow Circuit Bellmore WA 6150</p>
    <p>PO Box 2274 Bellmore DC WA 6971</p>
  </div>

  <ul class="contacts">
    <li>
      <svg class="icon" viewBox="0 0 16 16"><circle cx="8" cy="8" r="8" fill="var(--orange)"/><path d="M5 4l2 2-1 1a6 6 0 0 0 3 3l1-1 2 2-1.5 1.5C7 12 4 9 3.5 5.5z" fill="#fff"/></svg>
      08 9300 4417
    </li>
    <li>
      <svg class="icon" viewBox="0 0 16 16"><rect x="4" y="1" width="8" height="14" rx="1.5" fill="var(--orange)"/><rect x="5.5" y="3" width="5" height="7" fill="#fff"/></svg>
      123-456-7890
      <span class="fax">
        <svg class="icon" viewBox="0 0 16 16"><rect x="1" y="6" width="14" height="8" rx="1.5" fill="var(--orange)"/><rect x="4" y="2" width="8" height="5" fill="var(--orange)"/><rect x="4" y="9" width="8" height="2" fill="#fff"/></svg>
        08 9300 4418
      </span>
    </li>
    <li>
      <svg class="icon" viewBox="0 0 16 16"><circle cx="8" cy="8" r="8" fill="var(--orange)"/><rect x="3.5" y="5" width="9" height="6" fill="#fff"/><path d="M3.5 5l4.5 3.5L12.5 5" stroke="var(--orange)" fill="none"/></svg>
      sales@tarvoplastics.com.au
    </li>
  </ul>

  <div class="rule-top"></div>
  <div class="nameband">Your Name, <span class="title">Title</span></div>
  <div class="rule-bottom"></div>

  <p class="legal">Keelan Holdings Pty Ltd T/A Tarvo Plastics ABN: TBA</p>
</section>

<section class="card card--back" aria-label="Business card back">
  <div class="offer">
    <p class="offer__lead">The Products And Services That We Offer<br>Are Supplied From Diy To Trade &amp; Industrial Engineering Markets</p>

    <h2 class="offer__heading">We specialise in:</h2>
    <ul class="offer__list">
      <li><span>Cut to size panels (all shapes and sizes)</span></li>
      <li><span>Plastics fabrication &amp; Welding</span><span>Custom Designs</span></li>
      <li><span>Plastic Repairs</span><span>PVC Pipe Slotting &amp; PVC Pipe Threading</span></li>
      <li><span>Supplier of all types of engineering plastics and profiles</span></li>
    </ul>

    <h2 class="offer__heading">Including:</h2>
    <ul class="offer__list">
      <li><span>Acrylic / Clarvene</span><span>Polycarbonate / Dorvil</span></li>
      <li><span>Prismatic Light Diffuser</span><span>Vantrib</span><span>HDPE / UHMWPE</span></li>
      <li><span>PVC / PVC Foam</span><span>Nylon</span><span>HIPS</span></li>
    </ul>
  </div>
</section>

</body>
</html>
```